Restaurant Finder Website Design

I need to create a website that will help people find restaurants around a zip code or address.

I would like to have a very clean and simple design. I will need a design for the homepage, that should be very clean and simple to use. its where the users will launch their search. I am thinking something like tavuro like.. big search field with a very clean page where users can create an account or restaurants subscribe to the service.

Also need the design of the search results page, I would like to display a big map with the results and a list on the side or the bottom of the map.

Also need a profile page for the users that sign up to the site.

Mostly what I need are guidelines and color coordinated elements, like a general layout and buttons that work together. I would like to know what the action buttons and elements should look like. Because its going to have some more detail pages.

Target Market(s)

People in general, mainly people that work at an office and have to find a place for lunch every day.

Industry/Entity Type

Restaurant

Number of Pages Required

4 page

Font styles to use
Serif
Sans Serif

Requirements
Must have
• It must be a really simple and clean design but look edgy.

```html
<!DOCTYPE html>
<html lang="en">
<head>
<meta charset="UTF-8">
<title>Platewise – Find restaurants around you</title>
<link rel="stylesheet" href="https://fonts.googleapis.com/css2?family=Open+Sans:wght@400&family=Varela+Round&display=swap">
<style>
  :root {
    --brand-red: #c52026;
    --ink: #23252b;
    --black: #000000;
    --white: #ffffff;
    --placeholder: #666666;
    --divider: #8a1217;
  }
  * { box-sizing: border-box; margin: 0; padding: 0; }
  html, body {
    width: 1200px;
    height: 655px;
    overflow: hidden;
    background: var(--white);
    font-family: "Open Sans", Arial, sans-serif;
    color: var(--ink);
  }
  .page { position: relative; width: 1200px; height: 655px; }

  .brand {
    position: absolute;
    left: 454px;
    top: 122px;
    height: 102px;
    display: flex;
    align-items: center;
    gap: 16px;
  }
  .brand-mark {
    width: 86px;
    height: 86px;
    border-radius: 50%;
    background: var(--brand-red);
  }
  .brand-name {
    font-family: "Varela Round", Arial, sans-serif;
    font-size: 42px;
    color: var(--ink);
    letter-spacing: -0.5px;
  }

  .search-panel {
    position: absolute;
    left: 227px;
    top: 256px;
    width: 732px;
    height: 184px;
    background: var(--brand-red);
    color: var(--white);
  }
  .search-panel__title {
    position: absolute;
    left: 26px;
    top: 21px;
    font-family: "Varela Round", Arial, sans-serif;
    font-size: 20.5px;
    font-weight: 400;
    letter-spacing: -0.2px;
  }
  .search-form {
    position: absolute;
    left: 31px;
    top: 66px;
    width: 674px;
    height: 50px;
    display: flex;
  }
  .search-form__field {
    flex: 1;
    height: 50px;
    border: 0;
    background: var(--white);
    padding-left: 28px;
    font-family: "Open Sans", Arial, sans-serif;
    font-size: 17px;
    color: var(--ink);
    outline: none;
  }
  .search-form__field::placeholder { color: var(--placeholder); }
  .search-form__button {
    width: 122px;
    height: 50px;
    border: 0;
    background: var(--black);
    color: var(--white);
    font-family: "Varela Round", Arial, sans-serif;
    font-size: 21px;
    letter-spacing: 0.5px;
  }
  .search-form__icon {
    position: absolute;
    left: -16px;
    top: 9px;
    width: 32px;
    height: 32px;
  }
  .account-links {
    position: absolute;
    left: 0;
    right: 0;
    top: 139px;
    text-align: center;
    font-size: 15px;
  }
  .account-links a { color: var(--white); text-decoration: none; }
  .account-links .divider { color: var(--divider); margin: 0 4px; }

  .site-footer {
    position: absolute;
    left: 0;
    right: 0;
    top: 621px;
    text-align: center;
    font-size: 13.5px;
    color: var(--black);
  }
</style>
</head>
<body>
<div class="page">
  <header class="brand">
    <span class="brand-mark"></span>
    <span class="brand-name">Platewise</span>
  </header>

  <section class="search-panel">
    <h1 class="search-panel__title">We help people find restaurants arround a zip code or address</h1>
    <form class="search-form">
      <svg class="search-form__icon" viewBox="0 0 32 32" aria-hidden="true">
        <circle cx="16" cy="16" r="16" fill="#000"/>
        <circle cx="14.2" cy="14.2" r="5.2" fill="none" stroke="#fff" stroke-width="2.2"/>
        <line x1="18" y1="18" x2="22.5" y2="22.5" stroke="#fff" stroke-width="2.6" stroke-linecap="round"/>
      </svg>
      <input class="search-form__field" type="text" placeholder="Enter your zip code or Address">
      <button class="search-form__button" type="button">SEARCH</button>
    </form>
    <nav class="account-links">
      <a href="#">Create your account</a><span class="divider">|</span><a href="#">Login your account</a>
    </nav>
  </section>

  <footer class="site-footer">© 2016 Copyright Platewise All Rights Reserved</footer>
</div>
</body>
</html>
```